Website redesign for a Medical Office

We are a physician office in need of a website redesign and a face-lift.
1.Website must work on all platforms including mobile phones and tablets.
2.Website will also include and interactive CONTACT US form and payment gateway for office to collect payment from patients online.
3.Website should have the ability for us to easily edit content without resorting to the services of an IT person.
4. Website content will be collected from the present website www.sunbrookkids.com.
- The type of upgrade we are looking for is more of a corrective work. The major problems with the current website are:
1. Contact Us form not working correctly
2. Credit card/monetrix gateway not working as intended
3. Needing better images/pictures to correctly reflect our business.
4. General enhancement to the overall feel and outlook of the current website.

5. Once a design is selected, website MUST be up and live within TWO WEEKS. The designer able to make this work within the time-frame will get an extra bonus.

Target Market(s)

General public; including patients and their parents.

Industry/Entity Type

Healthcare

Coding

Coded - Design and coding required

Number of Pages Required

5+ page

Font styles to use
Sans Serif

Colors
0492cd
33a6d7
85cae6
cee9f5
cedeed
acd036
cadf82
00a990
f04a50

Requirements
Must have
• 1. Ability for the website to work on all platforms including mobile phones and tablets.
• 2. Include an interactive CONTACT US form
• 3. A payment gateway for office to collect payment from patients online using credit cards and Monetrix.
• 4. Website should have the ability for us to easily edit content without resorting to the services of an IT person.
• 5. Once a design is selected, website MUST be up and live within TWO WEEKS.
• 6. Social network buttons.
• 7. A Vorlund map with office location or geo-tag and directions to office.
Nice to have
• Nice theme, children friendly with a flashy home page and inside pages.
• Attractive design with wow factor

```html
<!DOCTYPE html>
<html lang="en">
<head>
<meta charset="utf-8">
<title>Sunbrook Pediatrics</title>
<link href="https://fonts.googleapis.com/css2?family=Lato:wght@400;700;900&family=Open+Sans:wght@400;600;700&display=swap" rel="stylesheet">
<style>
:root{
  --blue:#0492cd;--blue-2:#33a6d7;--blue-3:#85cae6;--blue-4:#cee9f5;--blue-5:#cedeed;
  --green:#acd036;--teal:#00a990;--red:#f04a50;--navy:#1a1fb8;
  --ink:#333;--muted:#888;--soft:#f6f6f8;--line:#e2e2e6;
}
*{box-sizing:border-box;margin:0;padding:0}
html,body{width:1200px;height:2616px;overflow:hidden}
body{position:relative;font-family:"Open Sans",Arial,sans-serif;color:var(--ink);background:#fff}
.abs{position:absolute}
.topbar{left:0;top:0;width:1200px;height:35px;background:var(--blue);color:#fff;font-size:11px;font-weight:600}
.topbar span{position:absolute;top:10px}
.topbar .dot{position:absolute;display:block;width:9px;height:9px;border-radius:50%;background:#fff;top:13px}
.header{left:0;top:35px;width:1200px;height:101px;background:#fff;box-shadow:0 2px 4px rgba(0,0,0,.12);z-index:2}
.brand{display:flex;align-items:center;gap:10px;position:absolute}
.brand-mark{width:50px;height:50px;background:var(--navy);border-radius:4px}
.brand-name{font-family:Lato,sans-serif;font-weight:900;color:var(--navy);font-size:20px;line-height:1.1;letter-spacing:1px;text-transform:uppercase}
.nav{position:absolute;left:454px;top:41px;display:flex;gap:24px;font-size:12.5px;color:#333;white-space:nowrap}
.nav .active{color:var(--blue)}
.hero{left:0;top:136px;width:1200px;height:523px;background:linear-gradient(90deg,#dde8f1 0%,#e9eff4 40%,#d6c7be 70%,#efe7e2 100%)}
.hero-title{left:131px;top:222px;font-family:Lato,sans-serif;color:var(--blue);text-transform:uppercase}
.hero-title .s{font-size:29px;font-weight:700;display:block}
.hero-title .l{font-size:39px;font-weight:700;display:block;margin-top:2px}
.hero-text{left:131px;top:327px;width:420px;font-size:16px;line-height:26px;color:#444}
.btn{left:131px;top:408px;width:167px;height:49px;background:var(--blue);color:#fff;border-radius:3px;font-family:Lato,sans-serif;font-weight:700;font-size:14px;display:flex;align-items:center;justify-content:center}
.dots{display:flex;gap:6px}
.dots i{width:9px;height:9px;border-radius:50%;background:#bbb;display:block}
.dots i.on{background:var(--blue)}
.services{left:131px;top:553px;width:938px;height:187px;display:flex;box-shadow:0 12px 14px -8px rgba(0,0,0,.25)}
.service{flex:1;color:#fff;text-align:center;padding-top:16px}
.service .icon{height:40px;display:flex;align-items:center;justify-content:center}
.service h3{font-family:Lato,sans-serif;font-size:20px;font-weight:700;margin:20px 0 8px}
.service p{font-size:13px;line-height:24px;opacity:.9;padding:0 20px}
.green{background:var(--green)}.teal{background:var(--teal)}.red{background:var(--red)}
.welcome{left:0;top:659px;width:1200px;height:440px;background:var(--soft);z-index:-1}
.h2{font-family:Lato,sans-serif;font-weight:700;font-size:29px;text-align:center;width:1200px;left:0;color:#333}
.lead{left:280px;top:872px;width:640px;text-align:center;font-size:12px;font-weight:700;line-height:24px;color:#333}
.body-text{left:131px;top:942px;width:938px;text-align:center;font-size:11px;line-height:23px;color:#999}
.arch h4{font-family:Lato,sans-serif;font-weight:700;color:var(--blue);font-size:19px;text-transform:uppercase;text-align:center}
.arch p{font-size:11px;line-height:24px;color:#666;text-align:center;margin-top:6px}
.arch{width:240px}
.testimonials{left:0;top:1680px;width:1200px;height:395px;background:var(--blue)}
.card{top:1798px;width:299px;height:201px;background:#fff;padding:18px 16px}
.avatar{width:56px;height:56px;background:linear-gradient(135deg,#c79a80,#6b4a3a);float:left;margin-right:16px}
.card h5{font-family:Lato,sans-serif;font-weight:700;font-size:15px;margin-top:2px}
.card small{display:block;font-size:10px;color:var(--muted);margin-top:10px}
.card p{clear:both;padding-top:16px;font-size:11px;line-height:22px;color:#555}
.map{left:0;top:2075px;width:1200px;height:260px;background:linear-gradient(135deg,#efece4,#f4efd6 45%,#e6e3dc)}
.footer{left:0;top:2335px;width:1200px;height:281px;background:var(--soft)}
.fhead{font-size:14px;color:#333;text-transform:uppercase}
.flist{font-size:11px;line-height:24px;color:#555}
.social{display:flex;gap:7px}
.social i{width:27px;height:27px;border-radius:50%;display:block}
.email{width:250px;height:35px;border:1px solid #ccc;background:#fff;font-size:11px;color:#666;padding:9px 12px;position:relative}
.contact-row{display:flex;gap:12px;font-size:11px;color:#555;line-height:16px;margin-bottom:8px}
.contact-row svg{flex:none;margin-top:1px}
.rule{left:131px;top:2560px;width:938px;height:1px;background:var(--line)}
.copy{left:0;top:2580px;width:1200px;text-align:center;font-size:10px;color:#444}
</style>
</head>
<body>

<div class="abs topbar">
  <i class="dot" style="left:133px"></i><span style="left:152px">OPENING HOURS : M-F 8:30AM - 5:30PM</span>
  <span style="left:380px">|</span>
  <i class="dot" style="left:397px"></i><span style="left:416px">CONTACT : (555) 014-2290</span>
  <i class="dot" style="left:1018px;width:8px;height:8px"></i><i class="dot" style="left:1035px;width:8px;height:8px"></i><i class="dot" style="left:1052px;width:8px;height:8px"></i>
</div>

<header class="abs header">
  <div class="brand" style="left:131px;top:25px"><span class="brand-mark"></span><span class="brand-name">Sunbrook<br>Pediatrics</span></div>
  <nav class="nav"><span class="active">Home</span><span>About Us</span><span>Our Services</span><span>Sunbrook Health Center</span><span>Forms</span><span>Latest News</span><span>Contact Us</span></nav>
</header>

<section class="abs hero" role="img" aria-label="Photo of a smiling toddler with a finger at the lips"></section>
<h1 class="abs hero-title"><span class="s">Medical Services</span><span class="l">That You Can Trust</span></h1>
<p class="abs hero-text">Routine Annual Physicals, Sports Physicals, School and College Physicals, Camp Physicals...</p>
<div class="abs btn">READ MORE</div>
<div class="abs dots" style="left:133px;top:486px"><i class="on"></i><i></i><i></i></div>

<div class="abs services">
  <div class="service green">
    <div class="icon"><svg width="38" height="34" viewBox="0 0 24 22"><path d="M12 21 2.5 11.5A5.5 5.5 0 0 1 12 4a5.5 5.5 0 0 1 9.5 7.5Z" fill="#fff"/></svg></div>
    <h3>GENERAL MEDICAL</h3><p>Routine Office visits for common ailment, Immunizations...</p>
  </div>
  <div class="service teal">
    <div class="icon"><svg width="26" height="38" viewBox="0 0 16 24"><circle cx="8" cy="3" r="3" fill="#fff"/><path d="M1 8h14v3h-4v13H9v-7H7v7H5V11H1Z" fill="#fff"/></svg></div>
    <h3>NEWBORN CARE</h3><p>Routine Office visits for common ailment, Immunizations...</p>
  </div>
  <div class="service red">
    <div class="icon"><svg width="40" height="36" viewBox="0 0 24 22"><rect x="1" y="5" width="22" height="16" rx="2" fill="#fff"/><rect x="8" y="1" width="8" height="5" rx="1" fill="none" stroke="#fff" stroke-width="2"/><path d="M10.5 9h3v3h3v3h-3v3h-3v-3h-3v-3h3Z" fill="#f04a50"/></svg></div>
    <h3>EMERGENCY CARE</h3><p>Routine Office visits for common ailment, Immunizations...</p>
  </div>
</div>

<div class="abs welcome"></div>
<h2 class="abs h2" style="top:808px">WELCOME TO SUNBROOK PEDIATRICS</h2>
<p class="abs lead">Sunbrook Pediatrics is a modern pediatric practice dedicated to the health and wellness of children. It is the pediatrician office of choice in Maple Ridge, Ohio.</p>
<p class="abs body-text">Sunbrook Pediatrics is a modern pediatric practice dedicated to the health and wellness of children. It is the pediatrician office of choice in Maple Ridge, Ohio. At Sunbrook Pediatrics, you will find a pediatrician and an environment that is warm and compassionate. All of our staff members are knowledgeable, caring, efficient, and ready to serve you.At Sunbrook Pediatrics, you will find a pediatrician and an environment that is warm and compassionate. All of our staff members are knowledgeable, caring, efficient, and ready to serve you. The general atmosphere is pleasant, flexible and fun-filled for you and your family to enjoy. It is our pleasure to provide you and your children with our wide range of services.</p>

<h2 class="abs h2" style="top:1164px">FROM OUR MEDICAL ARCHIVES</h2>
<svg class="abs" style="left:0;top:1230px" width="1200" height="360">
  <g stroke="#333" stroke-width="2" stroke-dasharray="2 4" fill="none">
    <line x1="340" y1="48" x2="388" y2="48"/><line x1="792" y1="48" x2="845" y2="48"/>
    <line x1="430" y1="65" x2="510" y2="125"/><line x1="750" y1="65" x2="690" y2="125"/>
    <line x1="430" y1="297" x2="510" y2="250"/><line x1="750" y1="297" x2="690" y2="250"/>
  </g>
  <g fill="#fff" stroke="#333" stroke-width="1.5">
    <circle cx="413" cy="48" r="25"/><circle cx="767" cy="48" r="25"/>
    <circle cx="413" cy="312" r="25"/><circle cx="767" cy="312" r="25"/>
  </g>
  <g fill="#0492cd">
    <circle cx="413" cy="40" r="6"/><rect x="403" y="48" width="20" height="12" rx="5"/>
    <circle cx="767" cy="34" r="5"/><path d="M762 41h8a6 6 0 0 1 0 14h-1v9h-7Z"/>
    <circle cx="409" cy="303" r="5"/><path d="M403 312h12l4 10h-4l-3-6-3 8h-5Z"/>
    <circle cx="763" cy="301" r="5"/><path d="M757 309h12v12h-12Z"/><circle cx="776" cy="322" r="4"/>
  </g>
  <rect x="506" y="122" width="192" height="183" rx="10" fill="var(--navy)"/>
</svg>
<div class="abs arch" style="left:122px;top:1268px"><h4>Health Basics</h4><p>Sunbrook Pediatrics is a modern pediatric practice dedicated to the health and wellness of children</p></div>
<div class="abs arch" style="left:843px;top:1268px"><h4>Pregnant</h4><p>Sunbrook Pediatrics is a modern pediatric practice dedicated to the health and wellness of children</p></div>
<div class="abs arch" style="left:122px;top:1484px"><h4>Common Illnesses</h4><p>Sunbrook Pediatrics is a modern pediatric practice dedicated to the health and wellness of children</p></div>
<div class="abs arch" style="left:843px;top:1484px"><h4>Newborn Care</h4><p>Sunbrook Pediatrics is a modern pediatric practice dedicated to the health and wellness of children</p></div>

<section class="abs testimonials"></section>
<h2 class="abs h2" style="top:1725px;color:#fff">TESTIMONIALS</h2>
<div class="abs card" style="left:131px"><div class="avatar" role="img" aria-label="Reviewer portrait"></div><h5>CHRISTOPHER</h5><small>CITY NAME, COUNTRY</small><p>Lorem ipsum dolor sit amet, consectetur adipiscing elit, sed do eiusmod tempor incididunt ut labore et dolore magna aliqua. Ut enim ad minim veniam, quis nostrud exercitation ullamco</p></div>
<div class="abs card" style="left:452px"><div class="avatar" role="img" aria-label="Reviewer portrait"></div><h5>CHRISTOPHER</h5><small>CITY NAME, COUNTRY</small><p>Lorem ipsum dolor sit amet, consectetur adipiscing elit, sed do eiusmod tempor incididunt ut labore et dolore magna aliqua. Ut enim ad minim veniam, quis nostrud exercitation ullamco</p></div>
<div class="abs card" style="left:773px"><div class="avatar" role="img" aria-label="Reviewer portrait"></div><h5>CHRISTOPHER</h5><small>CITY NAME, COUNTRY</small><p>Lorem ipsum dolor sit amet, consectetur adipiscing elit, sed do eiusmod tempor incididunt ut labore et dolore magna aliqua. Ut enim ad minim veniam, quis nostrud exercitation ullamco</p></div>
<div class="abs dots" style="left:564px;top:2035px"><i style="background:var(--blue-2)"></i><i style="background:#fff"></i><i style="background:var(--blue-2)"></i><i style="background:var(--blue-2)"></i><i style="background:var(--blue-2)"></i></div>

<div class="abs map" role="img" aria-label="Street map showing the office location"></div>

<footer class="abs footer"></footer>
<div class="brand" style="left:131px;top:2375px"><span class="brand-mark"></span><span class="brand-name">Sunbrook<br>Pediatrics</span></div>
<div class="abs social" style="left:131px;top:2455px"><i style="background:#3b5a98"></i><i style="background:#2aa6df"></i><i style="background:#0f77b5"></i><i style="background:#888"></i><i style="background:#f08a24"></i></div>

<div class="abs" style="left:441px;top:2368px"><div class="fhead">Sitemap</div><div class="flist" style="margin-top:18px">Home<br>Services<br>Contact<br>About Us<br>FAQ</div></div>
<div class="abs" style="left:581px;top:2368px"><div class="fhead">Newsletter</div><p class="flist" style="margin-top:18px;width:270px">Enter your email address to receive the latest news and notes from our blog.</p><div class="email" style="margin-top:14px">Email Id<span style="position:absolute;right:12px;top:7px;font-size:14px">›</span></div></div>
<div class="abs" style="left:903px;top:2368px;width:170px"><div class="fhead" style="margin-bottom:22px">Contact Us</div>
  <div class="contact-row"><svg width="12" height="12" viewBox="0 0 12 12"><path d="M1 3c2-2 8-2 10 0v2H8V4H4v1H1Zm1 3h8l1 5H1Z" fill="#444"/></svg>555-019-4471</div>
  <div class="contact-row"><svg width="12" height="12" viewBox="0 0 12 12"><rect x="3" y="1" width="6" height="3" fill="#444"/><rect x="1" y="4" width="10" height="5" fill="#444"/><rect x="3" y="8" width="6" height="3" fill="#888"/></svg>555-019-4471</div>
  <div class="contact-row"><svg width="12" height="12" viewBox="0 0 12 12"><rect x="1" y="2" width="10" height="8" fill="none" stroke="#444"/><path d="M1 2l5 4 5-4" fill="none" stroke="#444"/></svg><u>info@sunbrookkids.com</u></div>
  <div class="contact-row"><svg width="12" height="12" viewBox="0 0 12 12"><path d="M6 11S2 6.5 2 4.5a4 4 0 0 1 8 0C10 6.5 6 11 6 11Z" fill="#444"/><circle cx="6" cy="4.5" r="1.4" fill="#fff"/></svg>#2868 Lorem ipsum dolor sit amet, consectetur</div>
</div>
<div class="abs rule"></div>
<p class="abs copy">2017 © sunbrookkids.com. All Right Reserved.</p>

</body>
</html>
```